Dovin Sound 862 the new wave for sound to enlighten open ears

This is a music recording studio, we need pictures of a booth, random pictures of anything that will draw interest to a recording studio, we just need the website to reflect a music studio recording website. Apply generic information on the site that correlates with most music studio websites up to date. We want the modern style look that will entice eyes across the nation. Information should be easily accessible on the website. Dovin Sound 862 is owned by Marcellus Okafor located 5176 Bellweather Ln, Miramar, Fl, 33027. Email: Mokaforsound@trellomail.net and best contact number to date is 417-293-7041. The sound coming out of this location will be radio ready at all times, artist come in one way and come out with more wisdom than before. Its the new way to make music the appropriate way and bring the best out of those willing to reach their peak.

Target Market(s)

Recording Artist

Industry/Entity Type

Recording Studio

Coding

Coded - Design and coding required

Number of Pages Required

1 page

Font styles to use
Sans Serif

Requirements
Must have
• Anything that gives the site a music feel
Nice to have
• microphones, booths, studio mixing desk

```html
<!DOCTYPE html>
<html lang="en">
<head>
<meta charset="utf-8">
<title>Dovin Sound 862 — Music Recording Studio</title>
<link href="https://fonts.googleapis.com/css2?family=Roboto:wght@400;500;700&family=Open+Sans:wght@400;600;700&display=swap" rel="stylesheet">
<style>
:root{
  --teal:#3fbba5;
  --teal-dark:#2a8582;
  --navy:#0d3142;
  --navy-deep:#0a2533;
  --hero-a:#0f4a5c;
  --hero-b:#0b2b3a;
  --booth:#0e3a4c;
  --grey:#eeeeee;
  --line:#dddddd;
  --text:#555555;
  --head:#1f2a30;
  --white:#ffffff;
  --bar:#175b74;
}
*{margin:0;padding:0;box-sizing:border-box}
html,body{width:1200px;height:3152px;overflow:hidden;background:var(--white)}
body{position:relative;font-family:"Open Sans",Arial,sans-serif;color:var(--text)}
h1,h2,h3,.nav,.btn,.tab,.brand{font-family:"Roboto",Arial,sans-serif}

/* header */
.site-header{position:absolute;left:0;top:0;width:1200px;height:110px;background:linear-gradient(90deg,#2f8f86,#23757a);z-index:3}
.brand{position:absolute;display:flex;align-items:center;gap:14px;color:var(--white);font-weight:700;font-size:27px;line-height:28px;text-transform:uppercase}
.brand-mark{width:46px;height:46px;border-radius:50%;background:var(--white);flex:none}
.site-header .brand{left:99px;top:25px}
.nav{position:absolute;right:99px;top:70px;display:flex;gap:23px;list-style:none}
.nav li{color:var(--white);font-size:15px;font-weight:500;letter-spacing:.2px}
.socials{position:absolute;display:flex;gap:9px}
.socials span{width:35px;height:35px;border:2px solid var(--white);border-radius:50%;display:block}
.site-header .socials{right:115px;top:14px}

/* hero */
.hero{position:absolute;left:0;top:110px;width:1200px;height:527px;background:linear-gradient(100deg,var(--hero-a),var(--hero-b));clip-path:polygon(0 0,100% 0,100% 468px,50% 100%,0 468px)}
.hero h1{position:absolute;left:99px;top:108px;color:var(--white);font-size:46px;font-weight:500;letter-spacing:.5px}
.hero p{position:absolute;left:99px;top:172px;color:var(--white);font-family:"Roboto",sans-serif;font-size:32px}
.hero .btn-outline{position:absolute;left:99px;top:254px;width:153px;height:49px;border:2px solid var(--white);color:var(--white);font-size:17px;display:flex;align-items:center;justify-content:center}
.dots{position:absolute;left:99px;top:343px;display:flex;gap:5px}
.dots span{width:14px;height:14px;border-radius:50%;border:2px solid var(--white)}
.dots span:first-child{background:var(--teal);border-color:var(--teal)}
.hero-photo{position:absolute;left:715px;top:70px;width:390px;height:380px;border-radius:50%;background:radial-gradient(circle at 45% 45%,#3ab7f0 0%,#1a6a95 35%,rgba(11,43,58,0) 70%)}

/* section titles */
.sec-title{position:absolute;left:0;width:1200px;text-align:center;font-size:28px;font-weight:500;color:var(--teal)}
.sec-rule{position:absolute;left:532px;width:137px;height:2px;background:var(--teal)}

/* services */
.intro{position:absolute;left:220px;top:727px;width:760px;text-align:center;font-size:14px;line-height:27px}
.service{position:absolute;top:813px;width:250px;text-align:center}
.svc-icon{width:162px;height:162px;margin:0 auto;border:4px solid var(--navy);border-radius:50%;display:flex;align-items:center;justify-content:center}
.service.active .svc-icon{border-color:var(--teal);background:var(--teal);box-shadow:0 0 0 6px var(--white),0 0 0 9px var(--teal)}
.service h3{margin-top:28px;font-size:17px;font-weight:500;color:var(--head)}
.service.active h3{color:var(--teal)}
.service p{margin:14px auto 0;width:220px;font-size:13.5px;line-height:22px}
.btn-pill{display:inline-flex;align-items:center;justify-content:center;margin-top:18px;width:113px;height:40px;border:2px solid var(--navy);border-radius:20px;font-size:13px;font-weight:600;color:var(--head)}
.service.active .btn-pill{background:var(--teal);border-color:var(--teal);color:var(--white)}

/* booth */
.booth{position:absolute;left:0;top:1202px;width:1200px;height:521px;background:linear-gradient(180deg,#0f4457,var(--booth))}
.booth h2{position:absolute;left:0;top:66px;width:1200px;text-align:center;color:var(--white);font-size:28px;font-weight:500}
.booth .rule{position:absolute;left:532px;top:120px;width:137px;height:2px;background:var(--white)}
.booth-card{position:absolute;top:200px;width:320px;height:246px;border:4px solid var(--white);overflow:hidden}
.booth-photo{width:100%;height:100%}
.booth-card .label{position:absolute;left:0;bottom:0;width:100%;height:78px;background:var(--white);clip-path:polygon(0 100%,50% 0,100% 100%);display:flex;align-items:flex-end;justify-content:center;padding-bottom:10px;font-family:"Roboto",sans-serif;font-size:18px;color:var(--head)}

/* pricing */
.tabs{position:absolute;left:99px;top:1904px;width:1002px;height:71px;display:flex}
.tab{flex:1;background:var(--grey);display:flex;align-items:center;justify-content:center;font-size:24px;font-weight:500;color:var(--head)}
.tab.active{background:var(--teal);color:var(--white);position:relative}
.tab.active::after{content:"";position:absolute;left:50%;bottom:-22px;margin-left:-22px;border:22px solid transparent;border-bottom:0;border-top-color:var(--teal)}
.plan{position:absolute;top:2013px;width:290px;height:456px;background:var(--grey);padding:28px 20px 0;text-align:center}
.plan li{list-style:none;font-size:14px;line-height:26px;height:78px;padding-top:4px;border-bottom:1px solid #dcdcdc}
.plan li:last-of-type{border-bottom:0}
.plan .btn-pill{margin-top:18px;width:117px;height:38px;font-size:13px}
.plan.featured{top:2034px;width:326px;height:473px;background:var(--teal);color:var(--white);box-shadow:0 6px 14px rgba(0,0,0,.25);padding-top:42px;z-index:2}
.plan.featured li{border-bottom-color:rgba(255,255,255,.45)}
.badge{display:inline-block;width:136px;height:46px;line-height:46px;background:var(--white);color:var(--teal);font-family:"Roboto",sans-serif;font-weight:700;font-size:19px;margin-bottom:16px}
.plan.featured .btn-pill{border-color:var(--white);color:var(--white);margin-top:24px}

/* partners */
.divider{position:absolute;left:99px;top:2580px;width:1002px;height:2px;background:var(--line)}
.partner{position:absolute;top:2629px;width:134px;height:86px;border:1px solid var(--line);display:flex;align-items:center;justify-content:center}
.partner span{width:70px;height:22px;background:#cfd3d5;border-radius:3px}

/* footer */
.site-footer{position:absolute;left:0;top:2755px;width:1200px;height:334px;background:var(--navy)}
.site-footer .brand{left:99px;top:140px}
.f-col{position:absolute;top:50px;color:var(--white)}
.f-col h3{font-size:16px;font-weight:700;letter-spacing:.3px}
.quick li{list-style:none;font-size:14px;height:31.5px;line-height:31.5px}
.quick ul{margin-top:14px}
.contact-item{position:relative;padding-left:56px}
.contact-item .ico{position:absolute;left:0;top:0;width:40px;height:40px;border:2px solid var(--white);border-radius:50%;display:flex;align-items:center;justify-content:center}
.contact-item b{display:block;font-size:14px;font-weight:700;line-height:20px}
.contact-item small{display:block;font-size:12.5px;line-height:20px;white-space:nowrap}
.ci-address{margin-top:28px;height:80px}
.ci-phone{height:60px}
.ci-mail{height:60px}
.field{position:absolute;border:1px solid #8fa7b1;color:var(--white);font-size:11px;padding:8px 9px}
.send{position:absolute;left:847px;top:218px;width:120px;height:38px;border:2px solid var(--teal);color:var(--white);font-size:11px;display:flex;align-items:center;justify-content:center;font-family:"Roboto",sans-serif}
.bottom-bar{position:absolute;left:0;top:3089px;width:1200px;height:63px;background:var(--bar)}
.bottom-bar p{position:absolute;left:99px;top:21px;color:var(--white);font-size:13px;font-weight:600}
.bottom-bar .socials{right:99px;top:14px}
</style>
</head>
<body>

<header class="site-header">
  <div class="brand"><span class="brand-mark"></span><span>Dovin<br>Sound 862</span></div>
  <div class="socials"><span></span><span></span><span></span><span></span><span></span></div>
  <ul class="nav">
    <li>HOME</li><li>RECORDINGS</li><li>ABOUT US</li><li>PRICING</li><li>PORTFOLIO</li><li>BLOG</li><li>CONTACT</li>
  </ul>
</header>

<section class="hero">
  <div class="hero-photo" role="img" aria-label="Studio condenser microphone with headphones in blue light"></div>
  <h1>DOVIN SOUND 862</h1>
  <p>We are a music recording studio</p>
  <div class="btn-outline">RECORD NOW</div>
  <div class="dots"><span></span><span></span><span></span><span></span><span></span></div>
</section>

<h2 class="sec-title" style="top:670px">OUR MUSICAL SERVICES</h2>
<p class="intro">Nemo enim ipsam voluptatem quia voluptas sit aspernatur aut odit aut fugit, sed quia consequuntur magni dolores eos qui ratione voluptatem sequi nesciunt.</p>

<div class="service" style="left:186px">
  <div class="svc-icon">
    <svg width="70" height="70" viewBox="0 0 70 70"><rect x="18" y="6" width="46" height="46" fill="none" stroke="#0d3142" stroke-width="5"/><rect x="6" y="18" width="46" height="46" fill="#0d3142"/><path d="M24 52V32l16-4v18" stroke="#fff" stroke-width="3" fill="none"/><circle cx="21" cy="52" r="4" fill="#fff"/><circle cx="37" cy="47" r="4" fill="#fff"/></svg>
  </div>
  <h3>RECORDING STUDIO</h3>
  <p>Nemo enim ipsam voluptatem quia voluptas sit aspernatur aut odit aut fugit voluptatem.</p>
  <span class="btn-pill">Learn More</span>
</div>

<div class="service active" style="left:496px">
  <div class="svc-icon">
    <svg width="80" height="80" viewBox="0 0 80 80"><rect x="6" y="14" width="36" height="6" fill="#fff"/><rect x="6" y="28" width="36" height="6" fill="#fff"/><rect x="6" y="42" width="24" height="6" fill="#fff"/><path d="M44 62V14" stroke="#fff" stroke-width="5"/><circle cx="36" cy="62" r="10" fill="#fff"/><path d="M54 44l20 12-20 12z" fill="#fff"/></svg>
  </div>
  <h3>MUSIC STUDIO</h3>
  <p>Nemo enim ipsam voluptatem quia voluptas sit aspernatur aut odit aut fugit voluptatem.</p>
  <span class="btn-pill">Learn More</span>
</div>

<div class="service" style="left:764px">
  <div class="svc-icon">
    <svg width="76" height="70" viewBox="0 0 76 70"><circle cx="44" cy="35" r="28" fill="#0d3142"/><circle cx="44" cy="35" r="6" fill="#fff"/><rect x="2" y="5" width="42" height="60" fill="#0d3142" stroke="#fff" stroke-width="3"/><path d="M20 48V22l14-4v24" stroke="#fff" stroke-width="3" fill="none"/><circle cx="17" cy="48" r="4" fill="#fff"/><circle cx="31" cy="43" r="4" fill="#fff"/></svg>
  </div>
  <h3>MUSIC RECORDING</h3>
  <p>Nemo enim ipsam voluptatem quia voluptas sit aspernatur aut odit aut fugit voluptatem.</p>
  <span class="btn-pill">Learn More</span>
</div>

<section class="booth">
  <h2>OUR RECORDING BOOTH</h2>
  <div class="rule"></div>
  <div class="booth-card" style="left:99px">
    <div class="booth-photo" role="img" aria-label="Producer at keyboard and mixing desk in a recording studio" style="background:linear-gradient(135deg,#3b3f47,#7a5a4e 55%,#2a2e35)"></div>
    <div class="label">Recording Studio</div>
  </div>
  <div class="booth-card" style="left:439px">
    <div class="booth-photo" role="img" aria-label="Singer with guitar recording at a studio microphone" style="background:linear-gradient(135deg,#5a4a3e,#9a8370 50%,#3d342e)"></div>
    <div class="label">Music Recording</div>
  </div>
  <div class="booth-card" style="left:780px">
    <div class="booth-photo" role="img" aria-label="Headphones resting on a mixing console" style="background:linear-gradient(135deg,#2d5fa8,#d89a5a 55%,#3a4e7a)"></div>
    <div class="label">Music Studio</div>
  </div>
</section>

<h2 class="sec-title" style="top:1788px">OUR MUSICAL SERVICES</h2>
<div class="sec-rule" style="top:1840px"></div>

<div class="tabs">
  <div class="tab">RECORDING PRICE</div>
  <div class="tab active">MEMBERSHIPS DEALS</div>
  <div class="tab">MIX DOWN ONLY PRICES</div>
</div>

<div class="plan" style="left:147px">
  <ul>
    <li>$80 per hour minimum 4 hours<br>required</li>
    <li>75$ per hour minimum 8 hours<br>required</li>
    <li>$70 per hour minimum 12 hours<br>required</li>
    <li>$90 for individual hours , packages<br>recommended</li>
  </ul>
  <span class="btn-pill">GET NOW</span>
</div>

<div class="plan featured" style="left:437px">
  <span class="badge">POPULAR</span>
  <ul>
    <li>$1500, get 48 recording hours in addition<br>to 24 hours mix down</li>
    <li>$2500, get 72 recording hours in addition<br>to 48 hours mix down</li>
    <li>$3500, get 96 recording hours in addition<br>to 72 hours mix down</li>
  </ul>
  <span class="btn-pill">GET NOW</span>
</div>

<div class="plan" style="left:763px">
  <ul>
    <li>$50 per hour minimum 4 hours<br>required</li>
    <li>$45 per hour minimum 8 hours<br>required</li>
    <li>$40 per hour minimum 12 hours<br>required</li>
    <li>$60 for individual hours, packages<br>recommended</li>
  </ul>
  <span class="btn-pill">GET NOW</span>
</div>

<div class="divider"></div>
<div class="partner" style="left:99px"><span></span></div>
<div class="partner" style="left:273px"><span></span></div>
<div class="partner" style="left:447px"><span></span></div>
<div class="partner" style="left:620px"><span></span></div>
<div class="partner" style="left:794px"><span></span></div>
<div class="partner" style="left:967px"><span></span></div>

<footer class="site-footer">
  <div class="brand"><span class="brand-mark"></span><span>Dovin<br>Sound 862</span></div>

  <div class="f-col quick" style="left:393px">
    <h3>QUICK LINKS</h3>
    <ul><li>› Home</li><li>› Recordings</li><li>› Pricing</li><li>› About Us</li><li>› Portfolio</li><li>› Contact Us</li></ul>
  </div>

  <div class="f-col" style="left:578px;width:262px">
    <h3>CONTACT US</h3>
    <div class="contact-item ci-address">
      <span class="ico"><svg width="16" height="20" viewBox="0 0 16 20"><path d="M8 1a6 6 0 0 1 6 6c0 5-6 12-6 12S2 12 2 7a6 6 0 0 1 6-6z" fill="none" stroke="#fff" stroke-width="2"/><circle cx="8" cy="7" r="2" fill="#fff"/></svg></span>
      <b>COMPANY,</b><small>5176 Bellweather Ln, Lorrance,<br>Kv, 40219.</small>
    </div>
    <div class="contact-item ci-phone">
      <span class="ico"><svg width="12" height="18" viewBox="0 0 12 18"><rect x="1" y="1" width="10" height="16" rx="2" fill="none" stroke="#fff" stroke-width="2"/></svg></span>
      <b>PHONE:</b><small>417-293-7041</small>
    </div>
    <div class="contact-item ci-mail">
      <span class="ico"><svg width="18" height="14" viewBox="0 0 18 14"><rect x="1" y="1" width="16" height="12" fill="none" stroke="#fff" stroke-width="2"/><path d="M1 1l8 7 8-7" fill="none" stroke="#fff" stroke-width="2"/></svg></span>
      <b>Mail:</b><small>Mokaforsound@sonavemail.net</small>
    </div>
  </div>

  <div class="f-col" style="left:847px">
    <h3>CONTACT FORM</h3>
  </div>
  <div class="field" style="left:847px;top:95px;width:122px;height:36px">Name</div>
  <div class="field" style="left:977px;top:95px;width:124px;height:36px">Phone</div>
  <div class="field" style="left:847px;top:139px;width:254px;height:66px">Message</div>
  <div class="send">SEND MESSAGE</div>
</footer>

<div class="bottom-bar">
  <p>Copyright © 2017 Dovin Sound 862. All Right Reserved</p>
  <div class="socials"><span></span><span></span><span></span><span></span></div>
</div>

</body>
</html>
```